Request for Business Card Design

Hi. My name is Marlene, I am looking for a new business card design for my company, Quarrow Signal Instruments, LLC. I really like the design you did for Tarsel Venture and was hoping you could do something similar using our full logo and our mark. I am also open to any raised texture design using our mark. I have attached our full logo, which would need to be somewhere on the card, as well as the mark in both outline and full form, as well as our brand colors / guide. The card does not have to be white, as long as our logo and mark appear. I actually like darker colored business cards more, but am open to all options. If you are interested in working with me, please let me know. We would also take the business card design into letterhead design if you can do that.

```html
<!DOCTYPE html>
<html lang="en">
<head>
<meta charset="utf-8">
<title>Quarrow Signal Instruments – Business Card</title>
<link href="https://fonts.googleapis.com/css2?family=Montserrat:wght@400;500;700&display=swap" rel="stylesheet">
<style>
  :root {
    --stage: #d9d9d9;
    --paper: #ffffff;
    --ink: #2b2b2b;
    --muted: #5a5a5a;
    --brand-blue: #1a9bc4;
    --charcoal: #333336;
    --black: #111112;
    --faint: #e4edf5;
  }
  * { margin: 0; padding: 0; box-sizing: border-box; }
  html, body { width: 1200px; height: 786px; overflow: hidden; }
  body {
    background: var(--stage);
    font-family: "Montserrat", Arial, sans-serif;
    position: relative;
  }
  .card {
    position: absolute;
    top: 238px;
    width: 540px;
    height: 309px;
    overflow: hidden;
    box-shadow: 0 6px 18px rgba(0,0,0,.18);
  }
  /* ---------- Front ---------- */
  .card-front { left: 40px; background: var(--paper); }
  .front-decoration {
    position: absolute;
    right: -70px; top: 20px;
    width: 300px; height: 300px;
    border-radius: 50%;
    border: 18px solid var(--faint);
  }
  .brand { position: absolute; display: flex; align-items: center; gap: 12px; }
  .brand-dot { border-radius: 50%; background: var(--brand-blue); flex: none; }
  .brand-name { font-weight: 700; line-height: 1; }
  .brand-name .word { display: block; letter-spacing: 4px; }
  .brand-name .sub { display: block; letter-spacing: .6px; margin-top: 3px; }

  .card-front .brand { left: 28px; top: 58px; }
  .card-front .brand-dot { width: 40px; height: 40px; }
  .card-front .brand-name { color: var(--ink); }
  .card-front .brand-name .word { font-size: 32px; }
  .card-front .brand-name .sub { font-size: 9px; }

  .divider {
    position: absolute; left: 140px; top: 176px;
    width: 300px; height: 1px; background: var(--brand-blue);
  }
  .person { position: absolute; left: 28px; top: 186px; }
  .person-name { color: var(--brand-blue); font-weight: 700; font-size: 20px; }
  .person-role { color: var(--muted); font-size: 11px; margin-top: 1px; }
  .contacts { position: absolute; left: 28px; top: 234px; list-style: none; }
  .contacts li {
    display: flex; align-items: center; gap: 8px;
    font-size: 10.5px; color: var(--ink); height: 15px;
  }
  .contacts svg { width: 10px; height: 10px; fill: var(--brand-blue); flex: none; }
  .address {
    position: absolute; right: 28px; top: 210px;
    text-align: right; font-size: 11px; color: var(--ink); line-height: 1.45;
  }
  .band-blue {
    position: absolute; left: 0; bottom: 0;
    width: 66%; height: 9px; background: var(--brand-blue);
    clip-path: polygon(0 0, 100% 0, 97% 100%, 0 100%);
  }
  .band-dark {
    position: absolute; right: 0; bottom: 0;
    width: 38%; height: 20px; background: var(--charcoal);
    clip-path: polygon(4% 0, 100% 0, 100% 100%, 0 100%);
  }
  /* ---------- Back ---------- */
  .card-back {
    left: 620px;
    background: linear-gradient(135deg, #1c1c1e, var(--black));
  }
  .back-decoration {
    position: absolute; left: -90px; top: -60px;
    width: 400px; height: 400px; border-radius: 50%;
    background: radial-gradient(circle at 40% 40%, #3a3a3d 0%, #1d1d1f 60%, #141415 100%);
    box-shadow: inset 0 0 0 2px rgba(255,255,255,.08);
  }
  .card-back .brand { right: 26px; top: 124px; gap: 10px; }
  .card-back .brand-dot { width: 28px; height: 28px; }
  .card-back .brand-name { color: #ffffff; }
  .card-back .brand-name .word { font-size: 22px; letter-spacing: 3px; }
  .card-back .brand-name .sub { font-size: 6.5px; letter-spacing: .4px; }
</style>
</head>
<body>

<section class="card card-front" aria-label="Business card front">
  <div class="front-decoration" role="img" aria-label="Faint large brand mark decoration"></div>

  <div class="brand">
    <span class="brand-dot"></span>
    <span class="brand-name">
      <span class="word">QUARROW</span>
      <span class="sub">SIGNAL INSTRUMENTS</span>
    </span>
  </div>

  <div class="divider"></div>

  <div class="person">
    <p class="person-name">Daniel Reyes</p>
    <p class="person-role">Owner</p>
  </div>

  <ul class="contacts">
    <li>
      <svg viewBox="0 0 24 24"><path d="M6.6 10.8a15 15 0 0 0 6.6 6.6l2.2-2.2a1 1 0 0 1 1-.25 11.4 11.4 0 0 0 3.6.57 1 1 0 0 1 1 1V20a1 1 0 0 1-1 1A17 17 0 0 1 3 4a1 1 0 0 1 1-1h3.5a1 1 0 0 1 1 1c0 1.25.2 2.45.57 3.57a1 1 0 0 1-.25 1z"/></svg>
      +001 303 555 0142
    </li>
    <li>
      <svg viewBox="0 0 24 24"><path d="M2 5h20v14H2zm2 2v.4l8 5 8-5V7z"/></svg>
      info@quarrowsignal.com
    </li>
    <li>
      <svg viewBox="0 0 24 24"><path d="M12 2a10 10 0 1 0 0 20 10 10 0 0 0 0-20zm6.9 6h-3a15 15 0 0 0-1.3-4A8 8 0 0 1 18.9 8zM12 4a13 13 0 0 1 1.9 4h-3.8A13 13 0 0 1 12 4zM4.3 14a8 8 0 0 1 0-4h3.4a16 16 0 0 0 0 4zm.8 2h3a15 15 0 0 0 1.3 4A8 8 0 0 1 5.1 16zM8.1 8h-3a8 8 0 0 1 4.3-4 15 15 0 0 0-1.3 4zM12 20a13 13 0 0 1-1.9-4h3.8A13 13 0 0 1 12 20zm2.3-6H9.7a14 14 0 0 1 0-4h4.6a14 14 0 0 1 0 4zm.3 6a15 15 0 0 0 1.3-4h3a8 8 0 0 1-4.3 4zm1.7-6a16 16 0 0 0 0-4h3.4a8 8 0 0 1 0 4z"/></svg>
      www.quarrowsignal.com
    </li>
  </ul>

  <address class="address" style="font-style:normal">
    1180 Harlow Park Avenue<br>
    Fenwick, CO 80999
  </address>

  <div class="band-blue"></div>
  <div class="band-dark"></div>
</section>

<section class="card card-back" aria-label="Business card back">
  <div class="back-decoration" role="img" aria-label="Large raised brand mark decoration"></div>
  <div class="brand">
    <span class="brand-dot"></span>
    <span class="brand-name">
      <span class="word">QUARROW</span>
      <span class="sub">SIGNAL INSTRUMENTS</span>
    </span>
  </div>
</section>

</body>
</html>
```